www.lanternmerow.net

Hi,
UPDATE: Logo attached
TAG LINE NEW: OBITUARIES * CONDOLENCE NOTES
MULTIMEDIA MEMORIAL
Please refer to our existing site for more explanation of who we are?
We are a global data collecting portal site managing the Jewish funeral industry where users:
a) family and freinds in grief or "ancestry" searching persons
b) chevra kadisha's (funeral parlor)
c) current and historic cemetaries
d) Jewish Media Partners
arrive and choose a function (category):
in order to:
- upload a basic listing (FREE)
- upload/upgrade a multimedia listing (PAID)
- or search for a listing
of a deceased person (potentially millions of entries)
The functions (or categories) are accessed after the user:
Chooses their global location of search by
"Choose your Location" ie: Australia/NZ (which country?)
and allows the USER to choose a category function such as:
GROUP A (Local Info) GROUP B (Soul Search)
Chevra Kadisha Funerals (within 7 days)
Cemetaries Recently Deceased (up to 12mth)
Stonemasons Soul Search (after 1 year)
Jewish Media Partners
GROUP C (Jewish Death & Mourning Customs)
The way of Jewish burial
3000 y/old customs
When will Moshiach Come ?
Will I see my loved one again?
AIM:
To utilize existing logo and side menus (Member, Main & Resources) to create a user freindly and simpler friendly landing page, warmer and more softer for viewers.
To create logo buttons for the service catogories:
A, B & C and separate sub catagories
The MAIN AIM is to offer users opportunity to upload (LOG-IN required)
a) NEW basic FREE listing
b) NEW Multi-media PAID listing
SUMMARY:
1) User arrives at landing paid and sees global map, where he/she must choose the location in order to localize his data search
At this point, he/she can see what the site offers by the side MAIN, menu and icon function/catagories
(ie: Soul Search, New Basic Listing, Multimedia Listing)
2) After arriving at location (ie: Australia/NZ), the user then chooses the sub-function icon:
A- Local Funeral Service Info (Chevra Kadisha, Cemetary etc)
B- Soul Search (Funeral,Recently Deceased, Soul Search)
C- Jewish Death & Mourning Cutoms
Updates
Hi
Reason: Because of the holidays, we are happy to extend the deadline....
happy times
Target Market(s)
Family persons (Guest Member) & Industry (Members)
Industry/Entity Type
Industry
Requirements
Must have
- Style : Simple, Neat & Easy to Navigate
Icons: for each catagory/function
Colors; natural
-
Ability to bring inspiration, hope, light and healing to a difficult subject matter. (site look)
-
Education a profoundly deep 3000 y/old historically rich and mystic tradition to a wide audience
-
Allow children to access and upload data about grandparents etc
-
To promote on landing page the Invitation of local Chevra Kadisha's (funeral parlors), who have no web exposure, to get involved and LOG-IN and upload basic or multimedia listings.
(ie: please Register your local Chevra Kadisha here)
-
To promote on the landing page sample listings (Recently Deceased), to show look/feel of listings

```html
<!DOCTYPE html>
<html lang="en">
<head>
<meta charset="utf-8">
<title>LanternMerow.net — Obituaries · Condolence Notes · Multimedia Memorial</title>
<link rel="stylesheet" href="https://fonts.googleapis.com/css2?family=Cardo:wght@400;700&family=PT+Sans:wght@400;700&display=swap">
<style>
  :root {
    --ink: #2b2b2b;
    --ink-soft: #555555;
    --muted: #9a9a9a;
    --orange: #f08a1c;
    --orange-light: #fbb04a;
    --panel-dark: #3d3d3d;
    --field: #e6e6e6;
    --band-top: #e4e4e4;
    --band-bottom: #ffffff;
    --map-grey: #c4c4c4;
    --white: #ffffff;
    --social-blue: #3b5c9a;
    --social-sky: #4aa8d8;
    --social-orange: #f08a1c;
    --social-navy: #1f6fa8;
    --social-steel: #3c6f98;
  }
  * { box-sizing: border-box; margin: 0; padding: 0; }
  html, body { width: 1200px; height: 990px; overflow: hidden; background: var(--white); }
  body { position: relative; font-family: "PT Sans", Arial, sans-serif; color: var(--ink); }
  .abs { position: absolute; }

  /* Header */
  .brand { left: 48px; top: 28px; width: 200px; text-align: center; }
  .brand-flame { display: block; margin: 0 auto 8px; width: 16px; height: 16px; border-radius: 50%; background: var(--orange); }
  .brand-name { font-family: "Cardo", Georgia, serif; font-size: 22px; color: var(--ink); }

  .search { left: 725px; top: 18px; width: 226px; height: 30px; border-radius: 6px; background: var(--field);
            font-size: 13px; color: var(--muted); padding: 6px 12px; }
  .search svg { position: absolute; right: 8px; top: 5px; }

  .region-bar { left: 352px; top: 112px; width: 518px; height: 54px; border-radius: 8px;
                background: linear-gradient(#f4f4f4, #d9d9d9); box-shadow: 0 1px 3px rgba(0,0,0,.18); }
  .region-label { left: 50px; top: 14px; font-size: 22px; color: var(--ink-soft); }
  .region-select { left: 234px; top: 8px; width: 172px; height: 38px; border-radius: 8px; background: linear-gradient(#fafafa, #e8e8e8);
                   border: 1px solid #bdbdbd; font-size: 17px; padding: 8px 14px; color: var(--ink); }
  .region-select svg { position: absolute; right: 12px; top: 15px; }

  .login { left: 974px; top: 24px; width: 226px; height: 156px; background: var(--panel-dark); border-radius: 6px 0 0 6px; }
  .login-tab { left: 1075px; top: 0; width: 84px; height: 30px; background: var(--orange); color: var(--white);
               font-family: "Cardo", Georgia, serif; font-size: 22px; text-align: center; line-height: 28px; }
  .login-tab::after { content: ""; position: absolute; left: 34px; bottom: -8px; border: 8px solid transparent; border-bottom: 0; border-top-color: var(--orange); }
  .login-field { left: 24px; width: 182px; height: 30px; border-radius: 8px; background: var(--field); font-size: 15px; color: var(--ink-soft); padding: 6px 20px; }
  .signin { left: 78px; top: 96px; width: 82px; height: 28px; border-radius: 6px; background: linear-gradient(var(--orange-light), var(--orange));
            font-family: "Cardo", Georgia, serif; font-size: 20px; color: var(--white); text-align: center; line-height: 27px; }
  .register-note { left: 0; top: 130px; width: 226px; text-align: center; font-size: 13px; color: var(--white); }

  /* Main navigation */
  .nav-band { left: 0; top: 202px; width: 1200px; height: 44px; background: linear-gradient(var(--band-top), var(--band-bottom)); }
  .main-nav { left: 290px; top: 202px; display: flex; font-family: "Cardo", Georgia, serif; font-size: 21px; color: var(--ink-soft); }
  .main-nav a { color: inherit; text-decoration: none; height: 42px; line-height: 42px; padding: 0 19px; }
  .main-nav .current { background: linear-gradient(#f3f3f3, #cfcfcf); }

  /* Map */
  .world-map { left: 204px; top: 276px; width: 780px; height: 342px; border-radius: 40px;
               background: radial-gradient(ellipse at center, var(--map-grey), #e2e2e2 70%, var(--white)); }

  /* Recent passings */
  .passings-title { left: 211px; top: 632px; font-family: "Cardo", Georgia, serif; font-size: 26px; color: var(--ink); font-weight: 400; }
  .passing-icon { left: 218px; top: 688px; width: 46px; height: 70px; border-radius: 10px; background: linear-gradient(#3a3a3a, #1c1c1c); }
  .passing-text { left: 290px; top: 688px; width: 740px; font-size: 15.5px; line-height: 22px; color: var(--ink); }
  .more-btn { left: 937px; top: 736px; width: 82px; height: 27px; border-radius: 5px; background: linear-gradient(var(--orange-light), var(--orange));
              font-family: "Cardo", Georgia, serif; font-size: 18px; color: var(--ink); text-align: center; line-height: 26px; }

  /* Media partners */
  .partners-band { left: 0; top: 792px; width: 1200px; height: 90px; background: linear-gradient(var(--band-top), var(--band-bottom) 40%, var(--band-bottom)); }
  .partners { left: 60px; top: 820px; width: 1030px; display: flex; justify-content: space-between; align-items: center;
              font-family: "Cardo", Georgia, serif; font-size: 22px; font-weight: 700; color: var(--ink); }
  .partners li { list-style: none; display: flex; align-items: center; gap: 8px; }
  .partner-mark { width: 14px; height: 14px; background: var(--ink); }

  /* Footer */
  .footer-band { left: 0; top: 882px; width: 1200px; height: 52px; background: linear-gradient(var(--band-top), var(--band-bottom));
                 border-bottom: 1px solid #dcdcdc; }
  .footer-nav { left: 190px; top: 896px; display: flex; gap: 42px; font-family: "Cardo", Georgia, serif; font-size: 21px; color: var(--ink-soft); }
  .footer-nav a { color: inherit; text-decoration: none; }
  .copyright { left: 19px; top: 952px; font-size: 14px; color: var(--muted); }
  .social { left: 964px; top: 946px; display: flex; gap: 13px; }
  .social span { width: 24px; height: 24px; border-radius: 3px; }
</style>
</head>
<body>

<header>
  <div class="abs brand">
    <span class="brand-flame"></span>
    <span class="brand-name">LanternMerow.net</span>
  </div>

  <div class="abs search">Search
    <svg width="22" height="22" viewBox="0 0 22 22" aria-hidden="true">
      <circle cx="9" cy="9" r="6" fill="none" stroke="#6b6b6b" stroke-width="2"/>
      <line x1="13.5" y1="13.5" x2="19" y2="19" stroke="#333" stroke-width="3" stroke-linecap="round"/>
    </svg>
  </div>

  <div class="abs region-bar">
    <span class="abs region-label">Choose Region :</span>
    <div class="abs region-select">Israel
      <svg width="16" height="9" viewBox="0 0 16 9" aria-hidden="true"><path d="M0 0h16L8 9z" fill="#333"/></svg>
    </div>
  </div>

  <div class="abs login">
    <div class="abs login-field" style="top:22px">Username</div>
    <div class="abs login-field" style="top:57px">Password</div>
    <div class="abs signin">Sign in</div>
    <div class="abs register-note">Please Register a Memorial Page Here</div>
  </div>
  <div class="abs login-tab">Login</div>
</header>

<div class="abs nav-band"></div>
<nav class="abs main-nav">
  <a class="current" href="#">Home</a>
  <a href="#">Local Information</a>
  <a href="#">Soul Search</a>
  <a href="#">Jewish Customs</a>
</nav>

<main>
  <div class="abs world-map" role="img" aria-label="Grey world map for choosing a region, with Israel marked"></div>

  <h2 class="abs passings-title">Recent Passings</h2>
  <div class="abs passing-icon" role="img" aria-label="Footprints icon"></div>
  <p class="abs passing-text">Lorem Ipsum is simply dummy text of the printing and typesetting industry. Lorem Ipsum has been the industry's standard dummy text ever</p>
  <div class="abs more-btn">more...</div>
</main>

<div class="abs partners-band"></div>
<ul class="abs partners" aria-label="Media partners">
  <li>Kehila Times</li>
  <li><span class="partner-mark"></span>Shalom Weekly</li>
  <li>The Community Herald</li>
  <li><span class="partner-mark"></span>Heritage Roots</li>
  <li>The Harbor Post</li>
</ul>

<footer>
  <div class="abs footer-band"></div>
  <nav class="abs footer-nav">
    <a href="#">Home</a>
    <a href="#">Our mission</a>
    <a href="#">About Us</a>
    <a href="#">Personal Media</a>
    <a href="#">Contact Us</a>
    <a href="#">On-line Forum</a>
  </nav>
  <p class="abs copyright">Copyright © 2011. www.lanternmerow.net</p>
  <div class="abs social" aria-label="Share links">
    <span style="background:var(--social-blue)" aria-label="Share link"></span>
    <span style="background:var(--social-sky)" aria-label="Share link"></span>
    <span style="background:var(--social-orange)" aria-label="Feed"></span>
    <span style="background:var(--social-navy)" aria-label="Share link"></span>
    <span style="background:var(--social-steel)" aria-label="Share link"></span>
  </div>
</footer>

</body>
</html>
```